Working Capital graphics

Our business advisory firm requires 9 images to be re-created and improved in the branding of our business.

The 9 images have been uploaded below and the colours and branding of the business can be found at the website www.tallowmereadvisory.com.au

```html
<!DOCTYPE html>
<html lang="en">
<head>
<meta charset="utf-8">
<title>Working Capital Graphics – Ostrevane</title>
<link rel="stylesheet" href="https://fonts.googleapis.com/css2?family=Montserrat:ital,wght@0,400;0,500;0,600;0,700;1,500;1,600;1,700&display=swap">
<style>
  :root{
    --orange:#F7941D;
    --sky:#00AEEF;
    --sky-soft:#3CCBF4;
    --royal:#1450C8;
    --mid:#3F78D6;
    --navy:#0C3A8C;
    --slate:#34506F;
    --ink:#123A7A;
    --text:#1B1B1B;
    --white:#FFFFFF;
  }
  html,body{margin:0;padding:0;width:1200px;height:1200px;overflow:hidden;background:var(--white);}
  svg.board{display:block;width:1200px;height:1200px;font-family:'Montserrat',sans-serif;}
  .frame{fill:none;stroke:var(--orange);stroke-width:2.5;}
  .link{fill:none;stroke:var(--sky);stroke-width:1.5;}
  .link-navy{fill:none;stroke:var(--ink);stroke-width:1.2;}
  .bar{fill:var(--sky);}
  .bar-text{fill:var(--white);font-style:italic;font-weight:600;}
  .head-blue{fill:var(--royal);font-weight:600;}
  .head-orange{fill:var(--orange);font-weight:500;}
  .num-ring{fill:var(--white);stroke:var(--orange);stroke-width:1.5;}
  .num{fill:var(--orange);font-style:italic;font-weight:500;text-anchor:middle;}
  .hub-ring{fill:var(--white);stroke:var(--orange);stroke-width:1.5;}
  .hub-core{fill:var(--sky);}
  .hub-text{fill:var(--white);font-style:italic;font-weight:500;text-anchor:middle;}
  .axis{stroke:var(--sky);stroke-width:2;fill:none;}
  .dash{stroke:var(--sky);stroke-width:1.5;stroke-dasharray:5 4;fill:none;}
  .vector{stroke:var(--sky);stroke-width:1.6;fill:none;}
  .chart-label{fill:var(--navy);font-weight:500;}
  .chart-letter{fill:var(--navy);font-weight:600;}
  .cycle-arrow{fill:none;stroke:var(--orange);stroke-width:6;}
  .gear-text{fill:var(--white);font-weight:400;text-anchor:middle;}
  .chevron{fill:var(--navy);stroke:var(--white);stroke-width:2;}
  .chev-text{fill:var(--white);font-style:italic;font-weight:500;text-anchor:middle;}
  .box-blue{fill:var(--sky);}
  .box-orange{fill:var(--orange);}
  .box-text{fill:var(--white);font-style:italic;font-weight:500;text-anchor:middle;}
  .legend{fill:var(--navy);font-weight:500;}
  .seg{fill:none;stroke-width:78;}
  .seg-text{fill:var(--white);font-weight:600;text-anchor:middle;}
  .flag-label{fill:var(--navy);font-weight:700;text-anchor:middle;}
  .big-orange{fill:var(--orange);font-weight:600;text-anchor:middle;}
  .step{fill:var(--navy);font-weight:600;text-anchor:middle;font-size:7.5px;}
  .cycle-title{fill:var(--orange);font-weight:600;text-anchor:middle;font-size:10.5px;}
  .tag{fill:var(--sky);}
  .tag-text{fill:var(--white);font-weight:600;text-anchor:middle;font-size:8px;}
  .brand{fill:var(--orange);font-weight:700;text-anchor:middle;}
  .sat-ring{fill:var(--white);stroke:var(--sky);stroke-width:3;}
  .sat-accent{fill:none;stroke:var(--orange);stroke-width:3;}
  .sat-text{fill:var(--text);font-weight:500;text-anchor:middle;font-size:13px;}
</style>
</head>
<body>
<svg class="board" viewBox="0 0 1920 1920" xmlns="http://www.w3.org/2000/svg">
  <defs>
    <marker id="tip-orange" viewBox="0 0 10 10" refX="5" refY="5" markerWidth="5" markerHeight="5" orient="auto">
      <path d="M0,0 L10,5 L0,10 Z" fill="#F7941D"/>
    </marker>
    <marker id="tip-small" viewBox="0 0 10 10" refX="8" refY="5" markerWidth="6" markerHeight="6" orient="auto">
      <path d="M0,0 L10,5 L0,10 Z" fill="#00AEEF"/>
    </marker>
    <marker id="tip-flow" viewBox="0 0 10 10" refX="5" refY="5" markerWidth="3.2" markerHeight="3.2" orient="auto">
      <path d="M0,0 L10,5 L0,10 Z" fill="#F7941D"/>
    </marker>
    <g id="gear">
      <circle r="86"/>
      <rect x="-11" y="-106" width="22" height="30" transform="rotate(0)"/>
      <rect x="-11" y="-106" width="22" height="30" transform="rotate(36)"/>
      <rect x="-11" y="-106" width="22" height="30" transform="rotate(72)"/>
      <rect x="-11" y="-106" width="22" height="30" transform="rotate(108)"/>
      <rect x="-11" y="-106" width="22" height="30" transform="rotate(144)"/>
      <rect x="-11" y="-106" width="22" height="30" transform="rotate(180)"/>
      <rect x="-11" y="-106" width="22" height="30" transform="rotate(216)"/>
      <rect x="-11" y="-106" width="22" height="30" transform="rotate(252)"/>
      <rect x="-11" y="-106" width="22" height="30" transform="rotate(288)"/>
      <rect x="-11" y="-106" width="22" height="30" transform="rotate(324)"/>
    </g>
    <g id="flag">
      <line x1="0" y1="0" x2="6" y2="24" stroke="#0C3A8C" stroke-width="2"/>
      <path d="M1,2 L18,-2 L14,5 L19,11 L3,13 Z" fill="#F7941D"/>
    </g>
  </defs>

  <!-- ========== Receivables tree ========== -->
  <g class="panel receivables">
    <rect class="frame" x="105" y="119" width="502" height="370"/>
    <text class="head-blue" x="127" y="148" font-size="10">Receivables</text>
    <text class="head-orange" x="212" y="146" font-size="10">Sub-process</text>
    <text class="head-orange" x="323" y="146" font-size="10">Drivers</text>
    <text class="head-orange" x="478" y="146" font-size="10">Sub-drivers</text>

    <path class="link" d="M185,297 H196 M196,189 V397 M196,189 H221 M196,294 H221 M196,397 H221"/>
    <path class="link" d="M263,189 H275 M275,169 V212 M275,169 H288 M275,190 H288 M275,212 H288"/>
    <path class="link" d="M263,294 H275 M275,272 V316 M275,272 H288 M275,294 H288 M275,316 H288"/>
    <path class="link" d="M263,397 H275 M275,377 V420 M275,377 H288 M275,399 H288 M275,420 H288"/>
    <path class="link" d="M403,273 H425 M425,193 V467 M425,193 H452 M425,211 H452 M425,236 H452 M425,254 H452 M425,296 H452 M425,314 H452 M425,332 H452 M425,357 H452 M425,375 H452 M425,393 H452 M425,430 H452 M425,448 H452 M425,467 H452 M403,377 H425 M403,399 H425"/>

    <circle class="hub-ring" cx="157" cy="297" r="28"/>
    <circle class="hub-core" cx="157" cy="297" r="23"/>
    <text class="hub-text" x="157" y="296" font-size="7">Inventory</text>
    <text class="hub-text" x="157" y="306" font-size="7">Drivers</text>

    <g class="subprocess" font-size="5" fill="#F7941D" text-anchor="middle">
      <circle class="num-ring" cx="242" cy="189" r="21"/><text x="242" y="191">APPROVAL</text>
      <circle class="num-ring" cx="242" cy="294" r="21"/><text x="242" y="296">SALES</text>
      <circle class="num-ring" cx="242" cy="397" r="21"/><text x="242" y="399">COLLECTIONS</text>
    </g>

    <g class="drivers">
      <circle class="num-ring" cx="295" cy="169" r="7"/><text class="num" x="295" y="172" font-size="8">1</text>
      <rect class="bar" x="303" y="163" width="100" height="11"/><text class="bar-text" x="309" y="171" font-size="6">Differentiated terms</text>
      <circle class="num-ring" cx="295" cy="190" r="7"/><text class="num" x="295" y="193" font-size="8">2</text>
      <rect class="bar" x="303" y="184" width="100" height="11"/><text class="bar-text" x="309" y="192" font-size="6">Customer agreements</text>
      <circle class="num-ring" cx="295" cy="212" r="7"/><text class="num" x="295" y="215" font-size="8">3</text>
      <rect class="bar" x="303" y="206" width="100" height="11"/><text class="bar-text" x="309" y="214" font-size="6">Account st-up</text>
      <circle class="num-ring" cx="295" cy="272" r="7"/><text class="num" x="295" y="275" font-size="8">4</text>
      <rect class="bar" x="303" y="266" width="100" height="11"/><text class="bar-text" x="309" y="274" font-size="6">Receipt process</text>
      <circle class="num-ring" cx="295" cy="294" r="7"/><text class="num" x="295" y="297" font-size="8">5</text>
      <rect class="bar" x="303" y="288" width="100" height="11"/><text class="bar-text" x="309" y="296" font-size="6">Time to invoice</text>
      <circle class="num-ring" cx="295" cy="316" r="7"/><text class="num" x="295" y="319" font-size="8">6</text>
      <rect class="bar" x="303" y="310" width="100" height="11"/><text class="bar-text" x="305" y="318" font-size="5.6">Customer payment behaviour</text>
      <circle class="num-ring" cx="295" cy="377" r="7"/><text class="num" x="295" y="380" font-size="8">7</text>
      <rect class="bar" x="303" y="371" width="100" height="11"/><text class="bar-text" x="309" y="379" font-size="6">Payment cycle</text>
      <circle class="num-ring" cx="295" cy="399" r="7"/><text class="num" x="295" y="402" font-size="8">8</text>
      <rect class="bar" x="303" y="393" width="100" height="11"/><text class="bar-text" x="309" y="401" font-size="6">Collections</text>
      <circle class="num-ring" cx="295" cy="420" r="7"/><text class="num" x="295" y="423" font-size="8">9</text>
      <rect class="bar" x="303" y="414" width="100" height="11"/><text class="bar-text" x="309" y="422" font-size="6">Penalties</text>
    </g>

    <g class="subdrivers" text-anchor="middle">
      <rect class="bar" x="452" y="187" width="121" height="11"/><text class="bar-text" x="512" y="195" font-size="7">Cash</text>
      <rect class="bar" x="452" y="205" width="121" height="11"/><text class="bar-text" x="512" y="213" font-size="7">Banking process</text>
      <rect class="bar" x="452" y="230" width="121" height="11"/><text class="bar-text" x="512" y="238" font-size="7">Sales delivery</text>
      <rect class="bar" x="452" y="248" width="121" height="11"/><text class="bar-text" x="512" y="256" font-size="7">Invoicing</text>
      <rect class="bar" x="452" y="290" width="121" height="11"/><text class="bar-text" x="512" y="298" font-size="7">KPI</text>
      <rect class="bar" x="452" y="308" width="121" height="11"/><text class="bar-text" x="512" y="316" font-size="7">Relationship</text>
      <rect class="bar" x="452" y="326" width="121" height="11"/><text class="bar-text" x="512" y="334" font-size="7">Pricing</text>
      <rect class="bar" x="452" y="351" width="121" height="11"/><text class="bar-text" x="512" y="359" font-size="7">Closing date</text>
      <rect class="bar" x="452" y="369" width="121" height="11"/><text class="bar-text" x="512" y="377" font-size="7">Time to process</text>
      <rect class="bar" x="452" y="387" width="121" height="11"/><text class="bar-text" x="512" y="395" font-size="7">Invoicing cycle</text>
      <rect class="bar" x="452" y="424" width="121" height="11"/><text class="bar-text" x="512" y="432" font-size="7">Tracking</text>
      <rect class="bar" x="452" y="442" width="121" height="11"/><text class="bar-text" x="512" y="450" font-size="7">Methods</text>
      <rect class="bar" x="452" y="461" width="121" height="11"/><text class="bar-text" x="512" y="469" font-size="7">Agencies</text>
    </g>
  </g>

  <!-- ========== Inventories tree ========== -->
  <g class="panel inventories">
    <rect class="frame" x="682" y="119" width="498" height="370"/>
    <text class="head-blue" x="706" y="153" font-size="17">INVENTORIES</text>
    <text class="head-orange" x="880" y="151" font-size="9.5">Driver Group</text>
    <text class="head-orange" x="1043" y="151" font-size="9.5">Sub-group</text>

    <path class="link" d="M811,325 H835 M835,214 V439 M835,214 H849 M835,297 H849 M835,372 H849 M835,439 H849"/>
    <path class="link" d="M964,214 H978 M978,179 V249 M978,179 H992 M978,202 H992 M978,226 H992 M978,249 H992"/>
    <path class="link" d="M964,297 H978 M978,273 V321 M978,273 H992 M978,297 H992 M978,321 H992"/>
    <path class="link" d="M964,372 H978 M978,345 V393 M978,345 H992 M978,369 H992 M978,393 H992"/>
    <path class="link" d="M964,439 H978 M978,415 V462 M978,415 H992 M978,439 H992 M978,462 H992"/>

    <circle class="hub-ring" cx="761" cy="320" r="51"/>
    <circle class="hub-core" cx="761" cy="320" r="45"/>
    <text class="hub-text" x="761" y="318" font-size="14">Inventory</text>
    <text class="hub-text" x="759" y="339" font-size="14">Drivers</text>

    <g class="driver-groups">
      <rect class="bar" x="877" y="204" width="87" height="20"/><circle class="num-ring" cx="863" cy="214" r="14"/><text class="num" x="863" y="220" font-size="15">10</text><text class="bar-text" x="890" y="218" font-size="11">Planning</text>
      <rect class="bar" x="877" y="287" width="87" height="20"/><circle class="num-ring" cx="863" cy="297" r="14"/><text class="num" x="863" y="303" font-size="15">11</text><text class="bar-text" x="884" y="301" font-size="11">Procurement</text>
      <rect class="bar" x="877" y="362" width="87" height="20"/><circle class="num-ring" cx="863" cy="372" r="14"/><text class="num" x="863" y="378" font-size="15">12</text><text class="bar-text" x="890" y="376" font-size="11">Fulfilment</text>
      <rect class="bar" x="877" y="429" width="87" height="20"/><circle class="num-ring" cx="863" cy="439" r="14"/><text class="num" x="863" y="445" font-size="15">13</text><text class="bar-text" x="882" y="443" font-size="11">Product range</text>
    </g>

    <g class="sub-groups" text-anchor="middle">
      <rect class="bar" x="992" y="172" width="156" height="15"/><text class="bar-text" x="1070" y="183" font-size="9.5">Demand variability</text>
      <rect class="bar" x="992" y="195" width="156" height="15"/><text class="bar-text" x="1070" y="206" font-size="9.5">Planning collaboration</text>
      <rect class="bar" x="992" y="219" width="156" height="15"/><text class="bar-text" x="1070" y="230" font-size="9.5">Information availability</text>
      <rect class="bar" x="992" y="242" width="156" height="15"/><text class="bar-text" x="1070" y="253" font-size="9.5">Inventory target setting</text>
      <rect class="bar" x="992" y="266" width="156" height="15"/><text class="bar-text" x="1070" y="277" font-size="9.5">Order quantities</text>
      <rect class="bar" x="992" y="290" width="156" height="15"/><text class="bar-text" x="1070" y="301" font-size="9.5">Supplier lead time variability</text>
      <rect class="bar" x="992" y="314" width="156" height="15"/><text class="bar-text" x="1070" y="325" font-size="9.5">Supplier quality variability</text>
      <rect class="bar" x="992" y="338" width="156" height="15"/><text class="bar-text" x="1070" y="349" font-size="9.5">Customer service levels</text>
      <rect class="bar" x="992" y="362" width="156" height="15"/><text class="bar-text" x="1070" y="373" font-size="9.5">Network structure</text>
      <rect class="bar" x="992" y="386" width="156" height="15"/><text class="bar-text" x="1070" y="397" font-size="9.5">Inventory postponment</text>
      <rect class="bar" x="992" y="408" width="156" height="15"/><text class="bar-text" x="1070" y="419" font-size="9.5">Customer inventory needs</text>
      <rect class="bar" x="992" y="432" width="156" height="15"/><text class="bar-text" x="1070" y="443" font-size="9.5">Part standardisation</text>
      <rect class="bar" x="992" y="455" width="156" height="15"/><text class="bar-text" x="1070" y="466" font-size="9.5">SKU proliferation</text>
    </g>
  </g>

  <!-- ========== Payables tree ========== -->
  <g class="panel payables">
    <rect class="frame" x="1312" y="118" width="517" height="370"/>
    <text class="head-blue" x="1365" y="167" font-size="20">PAYABLES</text>
    <text class="head-orange" x="1605" y="187" font-size="14" letter-spacing="2">DRIVERS</text>

    <path class="link" d="M1467,338 H1492 M1492,227 V446 M1492,227 H1505 M1492,282 H1505 M1492,336 H1505 M1492,391 H1505 M1492,446 H1505"/>

    <circle class="hub-ring" cx="1417" cy="338" r="51"/>
    <circle class="hub-core" cx="1417" cy="338" r="45"/>
    <text class="hub-text" x="1416" y="332" font-size="13">Payable</text>
    <text class="hub-text" x="1417" y="351" font-size="13">Drivers</text>

    <g class="payable-drivers" text-anchor="middle">
      <rect class="bar" x="1533" y="217" width="246" height="20"/><circle class="num-ring" cx="1519" cy="227" r="14"/><text class="num" x="1519" y="233" font-size="15">14</text><text class="bar-text" x="1651" y="231" font-size="11">Reduce early payments</text>
      <rect class="bar" x="1533" y="272" width="246" height="20"/><circle class="num-ring" cx="1519" cy="282" r="14"/><text class="num" x="1519" y="288" font-size="15">15</text><text class="bar-text" x="1648" y="286" font-size="11">Reduce over-rides</text>
      <rect class="bar" x="1533" y="326" width="246" height="20"/><circle class="num-ring" cx="1519" cy="336" r="14"/><text class="num" x="1519" y="342" font-size="15">16</text><text class="bar-text" x="1648" y="340" font-size="11">Reduce vendor credits</text>
      <rect class="bar" x="1533" y="381" width="246" height="20"/><circle class="num-ring" cx="1519" cy="391" r="14"/><text class="num" x="1519" y="397" font-size="15">17</text><text class="bar-text" x="1656" y="395" font-size="11">increase PO vendor terms</text>
      <rect class="bar" x="1533" y="436" width="246" height="20"/><circle class="num-ring" cx="1519" cy="446" r="14"/><text class="num" x="1519" y="452" font-size="15">18</text><text class="bar-text" x="1654" y="450" font-size="11">Increase invoice only terms</text>
    </g>
  </g>

  <!-- ========== NWC absorption chart ========== -->
  <g class="panel nwc-chart">
    <rect class="frame" x="82" y="726" width="470" height="408"/>
    <text x="139" y="761" font-size="13" font-weight="700" font-style="italic" fill="#0C3A8C">NET WORKING CAPITAL ABSORPTION</text>

    <g class="chart-label" font-size="11" text-anchor="end">
      <text x="172" y="791">450m</text><text x="172" y="829">400m</text><text x="172" y="866">350m</text>
      <text x="172" y="903">300m</text><text x="172" y="941">250m</text><text x="172" y="978">200m</text>
      <text x="172" y="1016">150m</text><text x="172" y="1053">100m</text>
    </g>
    <g class="chart-label" font-size="11" text-anchor="middle">
      <text x="208" y="1081">20m</text><text x="253" y="1081">25m</text><text x="298" y="1081">30m</text>
      <text x="342" y="1081">35m</text><text x="387" y="1081">40m</text><text x="432" y="1081">45m</text>
    </g>
    <text x="326" y="1106" font-size="10.5" font-weight="700" fill="#0C3A8C" text-anchor="middle">NET WORKING CAPITAL (NWC)</text>
    <text x="128" y="918" font-size="11" font-weight="700" fill="#0C3A8C" text-anchor="middle" transform="rotate(-90 128 918)">SALES</text>

    <path class="axis" d="M183,780 V1064 H462"/>
    <path d="M325,918 L325,830 A88,88 0 1 0 413,918 Z" fill="#F7941D"/>
    <path class="dash" d="M183,918 H325 M325,918 V1064"/>

    <g class="vector" marker-end="url(#tip-small)">
      <line x1="325" y1="918" x2="325" y2="803"/>
      <line x1="325" y1="918" x2="255" y2="843"/>
      <line x1="325" y1="918" x2="386" y2="830"/>
      <line x1="325" y1="918" x2="434" y2="918"/>
      <line x1="325" y1="918" x2="391" y2="999"/>
      <line x1="325" y1="918" x2="242" y2="988"/>
    </g>
    <circle cx="325" cy="918" r="6" fill="#00AEEF"/>

    <g font-size="13">
      <text class="chart-letter" x="323" y="796">B</text>
      <text class="chart-letter" x="243" y="838">A</text>
      <text class="chart-letter" x="385" y="821">C</text>
      <text class="chart-letter" x="430" y="911">D</text>
      <text class="chart-letter" x="398" y="998">E</text>
      <text class="chart-letter" x="228" y="998">F</text>
    </g>
    <g class="chart-label" font-size="9" letter-spacing="0.6">
      <text x="202" y="818">OPTIMAL GROWTH</text>
      <text x="402" y="823">FAST GROWTH</text>
      <text x="447" y="902">DECLINING</text>
      <text x="447" y="915">GROWTH</text>
      <text x="416" y="998">CORPORATE STRESS</text>
      <text x="227" y="1019">DOWNSIZING</text>
    </g>
  </g>

  <!-- ========== Gear cycle ========== -->
  <g class="panel gear-cycle">
    <path class="cycle-arrow" d="M895,636 C990,595 1090,625 1118,720" marker-end="url(#tip-orange)"/>
    <path class="cycle-arrow" d="M704,852 C655,950 700,1060 792,1075" marker-end="url(#tip-orange)"/>
    <path class="cycle-arrow" d="M1155,998 C1180,1110 1100,1195 990,1183" marker-end="url(#tip-orange)"/>

    <use href="#gear" transform="translate(969,758) rotate(8)" fill="#00AEEF"/>
    <use href="#gear" transform="translate(832,918) rotate(14)" fill="#1450C8"/>
    <use href="#gear" transform="translate(1008,1037) rotate(4)" fill="#0C3A8C"/>

    <text class="gear-text" x="969" y="759" font-size="27">Accounts</text>
    <text class="gear-text" x="971" y="794" font-size="27">Receivable</text>
    <text class="gear-text" x="831" y="935" font-size="27">Inventory</text>
    <text class="gear-text" x="1007" y="1029" font-size="27">Accounts</text>
    <text class="gear-text" x="1007" y="1062" font-size="27">Payable</text>
  </g>

  <!-- ========== Value chain flow ========== -->
  <g class="panel value-chain">
    <rect class="frame" x="1262" y="735" width="565" height="369"/>

    <path class="link-navy" d="M1342,889 V913 M1436,839 V850 M1436,889 V913 M1384,913 V900 H1504 V889 M1504,900 V913 M1607,889 V913 M1681,842 V850 M1681,889 V913 M1739,889 V913 M1436,961 V981 M1681,961 V981 M1739,961 V981 M1444,961 V970 H1632 V961 M1488,961 V970 M1536,961 V970 M1586,961 V970"/>

    <g class="chevrons">
      <polygon class="chevron" points="1311,913 1352,913 1362,937 1352,961 1311,961"/>
      <polygon class="chevron" points="1360,913 1405,913 1415,937 1405,961 1360,961 1370,937"/>
      <polygon class="chevron" points="1413,913 1453,913 1463,937 1453,961 1413,961 1423,937"/>
      <polygon class="chevron" points="1461,913 1505,913 1515,937 1505,961 1461,961 1471,937"/>
      <polygon class="chevron" points="1513,913 1555,913 1565,937 1555,961 1513,961 1523,937"/>
      <polygon class="chevron" points="1563,913 1605,913 1615,937 1605,961 1563,961 1573,937"/>
      <polygon class="chevron" points="1613,913 1651,913 1661,937 1651,961 1613,961 1623,937"/>
      <polygon class="chevron" points="1659,913 1705,913 1715,937 1705,961 1659,961 1669,937"/>
      <polygon class="chevron" points="1716,913 1762,913 1772,937 1762,961 1716,961 1726,937"/>
    </g>
    <g font-size="5.5">
      <text class="chev-text" x="1334" y="940">Design</text>
      <text class="chev-text" x="1389" y="931">Order/</text><text class="chev-text" x="1389" y="939">Material</text><text class="chev-text" x="1389" y="947">Planning</text>
      <text class="chev-text" x="1440" y="940">Purchasing</text>
      <text class="chev-text" x="1490" y="940">Manufacturing</text>
      <text class="chev-text" x="1541" y="940">Pre-assembly</text>
      <text class="chev-text" x="1590" y="940">Assembly</text>
      <text class="chev-text" x="1638" y="936">Packaging/</text><text class="chev-text" x="1636" y="944">Shipping</text>
      <text class="chev-text" x="1686" y="940">Sales</text>
      <text class="chev-text" x="1744" y="935">After Sales/</text><text class="chev-text" x="1738" y="944">Service</text>
    </g>

    <g class="action-boxes" font-size="5.5">
      <rect class="box-orange" x="1311" y="850" width="66" height="39"/>
      <text class="box-text" x="1344" y="862">Reduce Part</text><text class="box-text" x="1344" y="871">Variants/</text><text class="box-text" x="1344" y="880">Releases</text>
      <rect class="box-blue" x="1408" y="800" width="57" height="39"/>
      <text class="box-text" x="1436" y="812">Modify</text><text class="box-text" x="1436" y="821">Payment</text><text class="box-text" x="1436" y="830">Conditions</text>
      <rect class="box-blue" x="1408" y="850" width="57" height="39"/>
      <text class="box-text" x="1436" y="862">Optimize</text><text class="box-text" x="1436" y="871">Payment</text><text class="box-text" x="1436" y="880">Process</text>
      <rect class="box-orange" x="1472" y="850" width="65" height="39"/>
      <text class="box-text" x="1504" y="862">Rethink Delivery</text><text class="box-text" x="1504" y="871">Schedules And</text><text class="box-text" x="1504" y="880">Warehousing</text>
      <rect class="box-blue" x="1574" y="850" width="66" height="39"/>
      <text class="box-text" x="1607" y="862">Optimize</text><text class="box-text" x="1607" y="871">Product</text><text class="box-text" x="1607" y="880">Product</text>
      <rect class="box-blue" x="1654" y="803" width="54" height="39"/>
      <text class="box-text" x="1681" y="815">Improve</text><text class="box-text" x="1681" y="824">Payment</text><text class="box-text" x="1681" y="833">Schemes</text>
      <rect class="box-blue" x="1654" y="850" width="54" height="39"/>
      <text class="box-text" x="1681" y="862">Reduce Due/</text><text class="box-text" x="1681" y="871">Overdue</text><text class="box-text" x="1681" y="880">Receivables</text>
      <rect class="box-blue" x="1713" y="850" width="53" height="39"/>
      <text class="box-text" x="1739" y="862">Establish New</text><text class="box-text" x="1739" y="871">Payment</text><text class="box-text" x="1739" y="880">Conditions</text>
      <rect class="box-orange" x="1408" y="981" width="57" height="39"/>
      <text class="box-text" x="1436" y="994">Optimize</text><text class="box-text" x="1436" y="1003">External</text><text class="box-text" x="1436" y="1012">Purchasing</text>
      <rect class="box-orange" x="1651" y="981" width="61" height="39"/>
      <text class="box-text" x="1681" y="994">Reduce</text><text class="box-text" x="1681" y="1003">Finished</text><text class="box-text" x="1681" y="1012">Goods Stocks</text>
      <rect class="box-orange" x="1713" y="981" width="56" height="39"/>
      <text class="box-text" x="1740" y="999">Reduce</text><text class="box-text" x="1740" y="1008">Inventory</text>
    </g>

    <g class="legend" font-size="5.8">
      <rect x="1522" y="1044" width="9" height="9" fill="#0C3A8C"/><text x="1536" y="1051">Inventory</text>
      <rect x="1579" y="1044" width="9" height="9" fill="#F7941D"/><text x="1594" y="1050">Payables And</text><text x="1594" y="1060">Prepayments Made</text>
      <rect x="1672" y="1044" width="9" height="9" fill="#00AEEF"/><text x="1687" y="1050">Receivables And</text><text x="1687" y="1060">Payments Received</text>
    </g>
  </g>

  <!-- ========== Sales volume wheel ========== -->
  <g class="panel sales-wheel">
    <g transform="translate(341,1546)">
      <circle class="seg" r="150" stroke="#3CCBF4" stroke-dasharray="102 1000" transform="rotate(-115)"/>
      <circle class="seg" r="150" stroke="#34506F" stroke-dasharray="142 1000" transform="rotate(-75)"/>
      <circle class="seg" r="150" stroke="#0C3A8C" stroke-dasharray="71 1000" transform="rotate(-20)"/>
      <circle class="seg" r="150" stroke="#0C3A8C" stroke-dasharray="69 1000" transform="rotate(8)"/>
      <circle class="seg" r="150" stroke="#3F78D6" stroke-dasharray="142 1000" transform="rotate(35)"/>
      <circle class="seg" r="150" stroke="#1450C8" stroke-dasharray="155 1000" transform="rotate(90)"/>
      <circle class="seg" r="150" stroke="#05A9EC" stroke-dasharray="168 1000" transform="rotate(150)"/>
      <circle class="seg" r="150" stroke="#18BBF2" stroke-dasharray="76 1000" transform="rotate(215)"/>
      <circle r="189" fill="none" stroke="#E4E8EE" stroke-width="3"/>
      <circle r="108" fill="#FFFFFF" stroke="#E6E6E6" stroke-width="9"/>
    </g>

    <g font-size="10">
      <text class="seg-text" x="319" y="1395">$0</text>
      <text class="seg-text" x="419" y="1417">COST OF SALES</text>
      <text class="seg-text" x="496" y="1520">OPERATING</text><text class="seg-text" x="496" y="1533">EXPENSES</text>
      <text class="seg-text" x="493" y="1592">FIXED</text><text class="seg-text" x="493" y="1605">COSTS</text>
      <text class="seg-text" x="450" y="1664">TAX</text>
      <text class="seg-text" x="420" y="1691">INTEREST</text>
      <text class="seg-text" x="377" y="1713">DIVIDENDS</text>
      <text class="seg-text" x="304" y="1703">INV</text><text class="seg-text" x="304" y="1716">DAYS</text>
      <text class="seg-text" x="253" y="1681">AP</text><text class="seg-text" x="253" y="1694">DAYS</text>
      <text class="seg-text" x="219" y="1645">AR</text><text class="seg-text" x="219" y="1658">DAYS</text>
      <text class="seg-text" x="183" y="1537">Additional</text><text class="seg-text" x="183" y="1550">Debt</text>
      <text class="seg-text" x="241" y="1417">CASH</text><text class="seg-text" x="246" y="1430">SHORTFALL</text>
    </g>

    <text class="brand" x="341" y="1500" font-size="13">Ostrevane</text>
    <text class="big-orange" x="339" y="1551" font-size="18.5">NEXT $100 OF</text>
    <text class="big-orange" x="339" y="1578" font-size="18.5">SALES VOLUME</text>

    <g font-size="10">
      <text class="flag-label" x="345" y="1337">REVENUE $0</text>
      <text class="flag-label" x="140" y="1415">AFTER</text><text class="flag-label" x="140" y="1427">ADDITIONAL</text><text class="flag-label" x="140" y="1439">FUNDING</text><text class="flag-label" x="137" y="1451" font-weight="500">$0</text>
      <text class="flag-label" x="557" y="1427">GROSS</text><text class="flag-label" x="557" y="1439">MARGIN</text><text class="flag-label" x="555" y="1451">$0</text>
      <text class="flag-label" x="129" y="1640">AFTER</text><text class="flag-label" x="133" y="1652">WORKING</text><text class="flag-label" x="130" y="1664">CAPITAL</text><text class="flag-label" x="126" y="1676">$0</text>
      <text class="flag-label" x="561" y="1657">EBIT</text><text class="flag-label" x="560" y="1669">$0</text>
      <text class="flag-label" x="358" y="1763">RETAINED</text><text class="flag-label" x="357" y="1775">INCOME $0</text>
    </g>
    <use href="#flag" x="80" y="1416"/>
    <use href="#flag" x="584" y="1423"/>
    <use href="#flag" x="80" y="1646"/>
    <use href="#flag" x="584" y="1646"/>
    <use href="#flag" x="302" y="1752"/>
  </g>

  <!-- ========== Process cycles ========== -->
  <g class="panel process-cycles">
    <g class="revenue-cycle">
      <text class="step" x="837" y="1307">CUSTOMER</text><text class="step" x="838" y="1321">STRATEGY</text>
      <text class="step" x="907" y="1313">SALES</text><text class="step" x="907" y="1325">MANAGEMENT</text>
      <text class="step" x="914" y="1342">RISK</text><text class="step" x="917" y="1354">MANAGEMENT</text>
      <text class="step" x="939" y="1377">CONTACT</text><text class="step" x="936" y="1389">MANAGEMENT</text>
      <text class="step" x="931" y="1414">SALES ORDER</text><text class="step" x="931" y="1426">PROCESSING</text>
      <text class="step" x="900" y="1453">CREDIT</text><text class="step" x="899" y="1465">CHECK</text>
      <text class="step" x="843" y="1468">ORDER</text><text class="step" x="843" y="1480">FULFILLMENT</text>
      <text class="step" x="781" y="1466">BILLING</text>
      <text class="step" x="752" y="1437">CUSTOMER</text><text class="step" x="752" y="1449">SERVICE</text>
      <text class="step" x="737" y="1395">CASH</text><text class="step" x="735" y="1407">COLLECTION</text>
      <text class="step" x="749" y="1354">RECEIPT &amp;</text><text class="step" x="746" y="1366">ALLOCATION</text><text class="step" x="750" y="1378">OF CASH</text>
      <text class="step" x="767" y="1319">CASH</text><text class="step" x="769" y="1331">MANAGEMENT</text>
      <g stroke="#F7941D" stroke-width="1.4" marker-end="url(#tip-flow)">
        <line x1="800" y1="1320" x2="812" y2="1316"/><line x1="861" y1="1316" x2="872" y2="1320"/>
        <line x1="886" y1="1330" x2="893" y2="1338"/><line x1="911" y1="1360" x2="913" y2="1372"/>
        <line x1="918" y1="1394" x2="915" y2="1404"/><line x1="907" y1="1431" x2="901" y2="1440"/>
        <line x1="880" y1="1463" x2="869" y2="1466"/><line x1="812" y1="1469" x2="802" y2="1464"/>
        <line x1="785" y1="1455" x2="778" y2="1447"/><line x1="760" y1="1424" x2="757" y2="1413"/>
        <line x1="755" y1="1389" x2="756" y2="1381"/><line x1="771" y1="1346" x2="776" y2="1336"/>
      </g>
      <text class="brand" x="835" y="1380" font-size="9">Ostrevane</text>
      <text class="cycle-title" x="835" y="1401">REVENUE</text><text class="cycle-title" x="835" y="1414">MANAGEMENT</text>
      <rect class="tag" x="783" y="1491" width="107" height="15"/><text class="tag-text" x="836" y="1501">CUSTOMER TO CASH</text>
    </g>

    <g class="supply-cycle">
      <text class="step" x="1180" y="1306">SUPPLY</text><text class="step" x="1178" y="1318">CHAIN</text><text class="step" x="1181" y="1330">STRATEGY</text>
      <text class="step" x="1245" y="1331">PRODUCT RANGE</text><text class="step" x="1247" y="1343">MANAGEMENT</text>
      <text class="step" x="1270" y="1366">FORECASTING</text>
      <text class="step" x="1275" y="1394">SALES ORDER</text><text class="step" x="1276" y="1406">FORECASTING</text>
      <text class="step" x="1258" y="1434">PRODUCTION</text><text class="step" x="1257" y="1447">SCHEDULING</text>
      <text class="step" x="1186" y="1466">RAW MATERIAL</text><text class="step" x="1183" y="1478">PLANNING</text>
      <text class="step" x="1110" y="1434">PRODUCTION</text><text class="step" x="1110" y="1447">PLANNING</text>
      <text class="step" x="1083" y="1399">PRODUCTION</text>
      <text class="step" x="1090" y="1367">WAREHOUSING</text>
      <text class="step" x="1118" y="1337">DISTRIBUTION</text>
      <g stroke="#F7941D" stroke-width="1.4" marker-end="url(#tip-flow)">
        <line x1="1141" y1="1321" x2="1152" y2="1317"/><line x1="1199" y1="1313" x2="1210" y2="1318"/>
        <line x1="1246" y1="1346" x2="1249" y2="1355"/><line x1="1259" y1="1371" x2="1259" y2="1382"/>
        <line x1="1257" y1="1410" x2="1254" y2="1420"/><line x1="1231" y1="1451" x2="1222" y2="1459"/>
        <line x1="1146" y1="1467" x2="1136" y2="1462"/><line x1="1103" y1="1421" x2="1101" y2="1411"/>
        <line x1="1098" y1="1386" x2="1098" y2="1376"/><line x1="1105" y1="1356" x2="1111" y2="1346"/>
      </g>
      <text class="brand" x="1185" y="1380" font-size="9">Ostrevane</text>
      <text class="cycle-title" x="1185" y="1401">SUPPLY CHAIN</text><text class="cycle-title" x="1185" y="1414">MANAGEMENT</text>
      <rect class="tag" x="1118" y="1491" width="135" height="15"/><text class="tag-text" x="1186" y="1501">FORECAST TO FULFILLMENT</text>
    </g>

    <g class="hub-triangle">
      <polygon points="1008,1478 929,1558 1087,1558" fill="#F7941D"/>
      <path d="M1008,1478 L1008,1528 M929,1558 L1008,1528 L1087,1558" stroke="#FFFFFF" stroke-width="2" fill="none"/>
      <text x="982" y="1518" fill="#FFFFFF" font-size="7" font-weight="600" text-anchor="middle" transform="rotate(-45 982 1518)">A/R</text>
      <text x="1036" y="1516" fill="#FFFFFF" font-size="7" font-weight="600" text-anchor="middle" transform="rotate(45 1036 1516)">INVENTORY</text>
      <text x="1008" y="1553" fill="#FFFFFF" font-size="7" font-weight="600" text-anchor="middle">A/P</text>
      <g stroke="#F7941D" stroke-width="4" marker-end="url(#tip-orange)">
        <line x1="952" y1="1500" x2="938" y2="1487"/>
        <line x1="1066" y1="1500" x2="1080" y2="1487"/>
        <line x1="1008" y1="1570" x2="1008" y2="1594"/>
      </g>
    </g>

    <g class="expenditure-cycle">
      <text class="step" x="998" y="1635">PURCHASING</text><text class="step" x="999" y="1648">STRATEGY</text>
      <text class="step" x="1071" y="1660">BUDGETING &amp;</text><text class="step" x="1072" y="1672">FORECASTING</text>
      <text class="step" x="1096" y="1694">ORIGINATING</text><text class="step" x="1096" y="1706">REQUIREMENTS</text>
      <text class="step" x="1092" y="1734">SELECTING &amp;</text><text class="step" x="1092" y="1746">NEGOTIATING</text>
      <text class="step" x="1071" y="1768">ORDERING &amp;</text><text class="step" x="1072" y="1780">CONTRACTING</text>
      <text class="step" x="1001" y="1792">RECEIVING &amp;</text><text class="step" x="1001" y="1804">EVALUATING</text>
      <text class="step" x="934" y="1770">DISCREPANCY</text><text class="step" x="935" y="1782">MANAGEMENT</text>
      <text class="step" x="912" y="1732">INVOICE</text><text class="step" x="912" y="1744">PROCESSING</text>
      <text class="step" x="908" y="1694">PAYMENT</text><text class="step" x="908" y="1706">ISSUANCE</text>
      <text class="step" x="941" y="1656">CASH</text><text class="step" x="941" y="1668">MANAGEMENT</text>
      <g stroke="#F7941D" stroke-width="1.4" marker-end="url(#tip-flow)">
        <line x1="957" y1="1650" x2="967" y2="1645"/><line x1="1033" y1="1643" x2="1043" y2="1649"/>
        <line x1="1071" y1="1677" x2="1075" y2="1686"/><line x1="1080" y1="1711" x2="1080" y2="1721"/>
        <line x1="1076" y1="1751" x2="1072" y2="1760"/><line x1="1046" y1="1784" x2="1037" y2="1789"/>
        <line x1="970" y1="1790" x2="961" y2="1785"/><line x1="930" y1="1759" x2="927" y2="1749"/>
        <line x1="918" y1="1722" x2="918" y2="1712"/><line x1="917" y1="1685" x2="922" y2="1676"/>
      </g>
      <text class="brand" x="1001" y="1700" font-size="9">Ostrevane</text>
      <text class="cycle-title" x="1001" y="1721">EXPENDITURE</text><text class="cycle-title" x="1001" y="1734">MANAGEMENT</text>
      <rect class="tag" x="950" y="1815" width="114" height="15"/><text class="tag-text" x="1007" y="1825">PURCHASE TO PAY</text>
    </g>
  </g>

  <!-- ========== Working capital hub ========== -->
  <g class="panel working-capital">
    <circle cx="1632" cy="1582" r="118" fill="none" stroke="#0C3A8C" stroke-width="3"/>
    <g fill="#1FA8E0">
      <circle cx="1632" cy="1464" r="4"/><circle cx="1709" cy="1492" r="4"/><circle cx="1749" cy="1560" r="4"/>
      <circle cx="1734" cy="1641" r="4"/><circle cx="1672" cy="1693" r="4"/><circle cx="1591" cy="1693" r="4"/>
      <circle cx="1528" cy="1641" r="4"/><circle cx="1515" cy="1560" r="4"/><circle cx="1556" cy="1492" r="4"/>
    </g>
    <circle cx="1632" cy="1582" r="107" fill="#22A9E1"/>
    <text x="1632" y="1574" fill="#FFFFFF" font-size="36" font-weight="500" text-anchor="middle">Working</text>
    <text x="1632" y="1622" fill="#FFFFFF" font-size="36" font-weight="500" text-anchor="middle">Capital</text>

    <g class="satellites">
      <circle class="sat-ring" cx="1632" cy="1375" r="55"/><path class="sat-accent" d="M1577,1375 A55,55 0 0 1 1632,1320"/>
      <text class="sat-text" x="1632" y="1358">Supply</text><text class="sat-text" x="1631" y="1380">Chain</text><text class="sat-text" x="1632" y="1403">Issues</text>

      <circle class="sat-ring" cx="1764" cy="1423" r="55"/><path class="sat-accent" d="M1764,1368 A55,55 0 0 1 1819,1423"/>
      <text class="sat-text" x="1766" y="1420">Process</text><text class="sat-text" x="1765" y="1443">Issues</text>

      <circle class="sat-ring" cx="1834" cy="1545" r="55"/><path class="sat-accent" d="M1779,1545 A55,55 0 0 1 1834,1490"/>
      <text class="sat-text" x="1835" y="1540">Forecasting</text><text class="sat-text" x="1835" y="1563">And Planning</text>

      <circle class="sat-ring" cx="1810" cy="1683" r="55"/><path class="sat-accent" d="M1810,1738 A55,55 0 0 1 1755,1683"/>
      <text class="sat-text" x="1810" y="1673">Customer</text><text class="sat-text" x="1811" y="1697">Management</text>

      <circle class="sat-ring" cx="1702" cy="1772" r="55"/><path class="sat-accent" d="M1757,1772 A55,55 0 0 1 1702,1827"/>
      <text class="sat-text" x="1703" y="1763">SKU</text><text class="sat-text" x="1703" y="1786">Complexity</text>

      <circle class="sat-ring" cx="1563" cy="1772" r="55"/><path class="sat-accent" d="M1563,1827 A55,55 0 0 1 1508,1772"/>
      <text class="sat-text" x="1563" y="1763">Supplier</text><text class="sat-text" x="1564" y="1786">Management</text>

      <circle class="sat-ring" cx="1455" cy="1683" r="55"/><path class="sat-accent" d="M1400,1683 A55,55 0 0 1 1455,1628"/>
      <text class="sat-text" x="1453" y="1678">KPIs And</text><text class="sat-text" x="1455" y="1701">Measures</text>

      <circle class="sat-ring" cx="1430" cy="1545" r="55"/><path class="sat-accent" d="M1430,1490 A55,55 0 0 1 1485,1545"/>
      <text class="sat-text" x="1430" y="1529">IT Systems</text><text class="sat-text" x="1430" y="1551">And</text><text class="sat-text" x="1430" y="1574">Information</text>

      <circle class="sat-ring" cx="1500" cy="1423" r="55"/><path class="sat-accent" d="M1500,1478 A55,55 0 0 1 1445,1423"/>
      <text class="sat-text" x="1499" y="1416">Terms And</text><text class="sat-text" x="1500" y="1440">Conditions</text>
    </g>
  </g>
</svg>
</body>
</html>
```